Business card design for Automotive workshop

We need a business card for a new automotive repair and tyre shop called Keelstone Prime Automotive located in New Zealand. We are a clean, modern and fresh workshop and company.

Front needs to feature logo,
my name:
Marlo Fenwicke (director)

Address:
48 Tarn Lane
Marrowby 3642

Phone: 07 594 2713
Mobile: 027 451 9362
Email: office@keelstoneautomotive.example.nz
Website: keelstoneautomotive.example.nz

Back needs to feature an area to write down appointment details, date and time.

Also feature a list of jobs and work we do such as,
Vehicle Servicing
All Mechanical Repairs
Warrant of Fitness
Tyres & Wheel Alignments
Automotive Diagnostics
Automotive Parts & Supplies

```html
<!DOCTYPE html>
<html lang="en">
<head>
<meta charset="utf-8">
<title>Keelstone Prime Automotive – Business Card</title>
<link href="https://fonts.googleapis.com/css2?family=Open+Sans:wght@400;600;700&family=Oswald:wght@500;600&display=swap" rel="stylesheet">
<style>
  :root {
    --bg: #8a8a8a;
    --card-dark: #232122;
    --card-light: #ffffff;
    --red: #e3262d;
    --ink: #1d1d1d;
    --grey-text: #555555;
    --white: #ffffff;
  }
  * { box-sizing: border-box; margin: 0; padding: 0; }
  html, body {
    width: 1200px; height: 960px; overflow: hidden;
    background: var(--bg);
    font-family: "Open Sans", Arial, sans-serif;
  }
  .canvas { position: relative; width: 1200px; height: 960px; }

  .card {
    position: absolute; width: 720px; height: 411px;
    box-shadow: 0 10px 24px rgba(0,0,0,.35);
  }

  /* Back side */
  .card-back { left: 80px; top: 50px; background: var(--card-dark); color: var(--white); }
  .card-back .brand {
    position: absolute; top: 48px; left: 0; right: 0; text-align: center;
    font-weight: 700; font-size: 40px; letter-spacing: 1px; color: var(--red);
    text-transform: uppercase; line-height: 1.1;
  }
  .card-back .brand-sub { display: block; font-size: 22px; letter-spacing: 6px; }
  .services { position: absolute; top: 150px; left: 0; right: 0; text-align: center; }
  .services-title { color: var(--red); font-weight: 700; font-size: 19px; text-transform: uppercase; margin-bottom: 6px; }
  .services-line { font-size: 16px; line-height: 1.45; }
  .services-line .dot { color: var(--red); margin: 0 6px; }
  .appointment {
    position: absolute; left: 0; right: 28px; bottom: 36px; height: 112px;
    background: var(--card-light); padding: 20px 34px;
  }
  .appt-row { display: flex; align-items: baseline; gap: 10px; height: 40px; }
  .appt-label { color: var(--red); font-weight: 600; font-size: 16px; }
  .appt-fill { flex: 1; border-bottom: 2px dotted #9a9a9a; height: 14px; }

  /* Front side */
  .card-front { left: 400px; top: 490px; background: var(--card-light); color: var(--ink); }
  .holder { position: absolute; top: 34px; right: 44px; text-align: right; font-family: "Oswald", Arial, sans-serif; line-height: 1.05; }
  .holder-name { color: var(--red); font-size: 26px; font-weight: 600; text-transform: uppercase; }
  .holder-role { font-size: 15px; font-weight: 500; text-transform: uppercase; }
  .card-front .brand {
    position: absolute; top: 118px; left: 150px; right: 40px; text-align: center;
    font-weight: 700; font-size: 40px; letter-spacing: 1px; color: var(--red);
    text-transform: uppercase; line-height: 1.1;
  }
  .card-front .brand-sub { display: block; font-size: 22px; letter-spacing: 6px; }
  .contact { position: absolute; left: 64px; bottom: 34px; color: var(--grey-text); font-size: 17px; line-height: 1.5; }
  .contact-row { display: flex; align-items: center; gap: 10px; }
  .contact-row svg { width: 15px; height: 15px; fill: var(--red); flex: none; }
  .address { margin-bottom: 4px; }
</style>
</head>
<body>
<main class="canvas">

  <section class="card card-back" aria-label="Card back">
    <div class="brand">Keelstone Prime<span class="brand-sub">Automotive</span></div>
    <div class="services">
      <div class="services-title">Vehicle Servicing</div>
      <div class="services-line">All Mechanical Repairs<span class="dot">•</span>Warrant of Fitness<span class="dot">•</span>Tyres &amp; Wheel Alignments</div>
      <div class="services-line">Automotive Diagnostics<span class="dot">•</span>Automotive Parts &amp; Supplies</div>
    </div>
    <div class="appointment">
      <div class="appt-row"><span class="appt-label">Date:</span><span class="appt-fill"></span><span class="appt-label">Time:</span><span class="appt-fill"></span></div>
      <div class="appt-row"><span class="appt-label">Date:</span><span class="appt-fill"></span><span class="appt-label">Time:</span><span class="appt-fill"></span></div>
    </div>
  </section>

  <section class="card card-front" aria-label="Card front">
    <div class="holder">
      <div class="holder-name">Marlo Fenwicke</div>
      <div class="holder-role">Director</div>
    </div>
    <div class="brand">Keelstone Prime<span class="brand-sub">Automotive</span></div>
    <div class="contact">
      <div class="address">48 Tarn Lane Marrowby 3642</div>
      <div class="contact-row">
        <svg viewBox="0 0 16 16" aria-hidden="true"><path d="M3.6 1.2l2.3 2.3-1.3 2a9 9 0 0 0 5.9 5.9l2-1.3 2.3 2.3-1.7 2.2C7.6 16 0 8.4.9 2.9z"/></svg>
        <span>07 594 2713</span>
      </div>
      <div class="contact-row">
        <svg viewBox="0 0 16 16" aria-hidden="true"><path d="M4 0h8a1 1 0 0 1 1 1v14a1 1 0 0 1-1 1H4a1 1 0 0 1-1-1V1a1 1 0 0 1 1-1zm1 2v10h6V2zm3 11a1 1 0 1 0 0 2 1 1 0 0 0 0-2z"/></svg>
        <span>027 451 9362</span>
      </div>
      <div class="contact-row">
        <svg viewBox="0 0 16 16" aria-hidden="true"><path d="M0 3h16v10H0zm1.5 1.2L8 9l6.5-4.8V4h-13z"/></svg>
        <span>office@keelstoneautomotive.example.nz</span>
      </div>
      <div class="contact-row">
        <svg viewBox="0 0 16 16" aria-hidden="true"><path d="M8 0a8 8 0 1 0 0 16A8 8 0 0 0 8 0zm0 1.5c.9 0 2 1.9 2.3 5H5.7C6 3.4 7.1 1.5 8 1.5zM5.7 8h4.6c-.3 3.1-1.4 5-2.3 5s-2-1.9-2.3-5z"/></svg>
        <span>www.keelstoneautomotive.example.nz</span>
      </div>
    </div>
  </section>

</main>
</body>
</html>
```